Business card for Luxury Portable Restroom Trailer company

We are a Luxury Portable Restroom Trailer Company Called FALCRIDGE HIRES. Based in Orange County California. We provide portable restroom trailers for events, such as, Weddings, Concerts, Charity events, Sporting events, Tournaments, Corporate events, ect. We rent and Sell the Luxury restrooms. Our colors are white, grey, and Orange. As you will see in the logo we uploaded.
There are 2 people in the company so the names and titles will change for the 3 people but card will remain the same. Here is the information for each Person: Dwight Penner CFO 555 318-0476
next Person: Leon Marchetti VP 555 318-0476
Next Person: Owen Marchetti CEO 555 318-0476
Information to include on the card: Luxury Restroom Trailers Rental and Sales. Weddings, Concerts, Charity, Sporting and Corp. Events.

```html
<!DOCTYPE html>
<html lang="en">
<head>
<meta charset="utf-8">
<title>FALCRIDGE HIRES – Business Card</title>
<link href="https://fonts.googleapis.com/css2?family=Open+Sans:wght@400;600;700;800&display=swap" rel="stylesheet">
<style>
  :root{
    --stage:#232323;
    --paper:#fdfcf4;
    --peach:#fbe6d4;
    --orange:#f0641e;
    --grey:#4a4a4a;
    --swoosh-light:#f1f1ec;
    --swoosh-shadow:#d6d6d0;
    --text:#2b2b2b;
  }
  *{margin:0;padding:0;box-sizing:border-box}
  html,body{width:1200px;height:768px;overflow:hidden;background:var(--stage)}
  body{font-family:"Open Sans",Arial,sans-serif;position:relative}
  .card{
    position:absolute;top:104px;width:340px;height:560px;
    background:var(--paper);border-radius:26px;overflow:hidden;
  }
  .card--front{left:220px}
  .card--back{left:640px}

  /* front */
  .front-decoration{
    position:absolute;inset:0;
    background:radial-gradient(ellipse at 55% 45%,var(--peach) 0%,var(--peach) 55%,rgba(251,230,212,0) 78%);
  }
  .front-logo{
    position:absolute;left:50%;top:50%;
    transform:translate(-50%,-50%) rotate(-90deg);
    display:flex;align-items:center;gap:12px;white-space:nowrap;
  }
  .logo-mark{width:22px;height:22px;background:var(--orange)}
  .logo-name{font-weight:800;color:var(--orange);letter-spacing:2px;text-transform:uppercase}
  .front-logo .logo-name{font-size:34px}

  /* back */
  .back-logo{
    position:absolute;top:44px;left:0;right:0;
    display:flex;justify-content:center;align-items:center;gap:10px;
  }
  .back-logo .logo-mark{width:14px;height:14px}
  .back-logo .logo-name{font-size:21px}

  .person{position:absolute;top:192px;left:0;right:0;text-align:center}
  .person-name{font-size:27px;font-weight:700;line-height:1.1}
  .person-name .first{color:var(--orange)}
  .person-name .last{color:var(--grey)}
  .person-title{font-size:15px;font-weight:600;color:var(--text);margin-top:2px}

  .contact-icons{display:flex;justify-content:center;gap:8px;margin-top:12px}
  .contact-icon{width:26px;height:26px;border-radius:50%;background:var(--orange);display:flex;align-items:center;justify-content:center}
  .contact-icon svg{width:14px;height:14px}
  .contact-lines{margin-top:10px;font-size:15px;color:var(--text);line-height:1.35}

  .swoosh{position:absolute;left:0;bottom:0;width:340px;height:250px}

  .services{
    position:absolute;left:0;right:0;bottom:38px;
    font-size:13px;color:var(--text);text-align:center;line-height:1.6;
  }
  .services li{display:inline;list-style:none;margin:0 5px}
  .services li::before{
    content:"";display:inline-block;width:8px;height:8px;border-radius:50%;
    background:var(--orange);margin-right:5px;vertical-align:1px;
  }
</style>
</head>
<body>

<section class="card card--front" aria-label="Card front">
  <div class="front-decoration" role="img" aria-label="Faint large rhino silhouette decoration in soft peach"></div>
  <div class="front-logo">
    <span class="logo-mark"></span>
    <span class="logo-name">Falcridge Hires</span>
  </div>
</section>

<section class="card card--back" aria-label="Card back">
  <div class="back-logo">
    <span class="logo-mark"></span>
    <span class="logo-name">Falcridge Hires</span>
  </div>

  <svg class="swoosh" viewBox="0 0 340 250" preserveAspectRatio="none" aria-hidden="true">
    <path d="M0 70 C90 110 230 90 340 0 L340 250 L0 250 Z" fill="var(--swoosh-shadow)"/>
    <path d="M0 78 C90 118 230 98 340 10 L340 250 L0 250 Z" fill="var(--swoosh-light)"/>
    <path d="M0 150 C120 110 250 120 340 70 L340 250 L0 250 Z" fill="var(--swoosh-shadow)" opacity=".55"/>
    <path d="M0 158 C120 118 250 128 340 80 L340 250 L0 250 Z" fill="var(--paper)"/>
  </svg>

  <div class="person">
    <h1 class="person-name"><span class="first">Dwight</span> <span class="last">Penner</span></h1>
    <p class="person-title">CFO</p>
    <div class="contact-icons">
      <span class="contact-icon"><svg viewBox="0 0 24 24"><path fill="#fff" d="M6.6 10.8a15 15 0 0 0 6.6 6.6l2.2-2.2c.3-.3.7-.4 1-.2 1.1.4 2.3.6 3.6.6.6 0 1 .4 1 1V20c0 .6-.4 1-1 1A17 17 0 0 1 3 4c0-.6.4-1 1-1h3.5c.6 0 1 .4 1 1 0 1.3.2 2.5.6 3.6.1.3 0 .7-.2 1z"/></svg></span>
      <span class="contact-icon"><svg viewBox="0 0 24 24"><rect x="3" y="6" width="18" height="12" rx="1.5" fill="none" stroke="#fff" stroke-width="2"/><path d="M3 7l9 6 9-6" fill="none" stroke="#fff" stroke-width="2"/></svg></span>
      <span class="contact-icon"><svg viewBox="0 0 24 24"><circle cx="12" cy="12" r="9" fill="none" stroke="#fff" stroke-width="2"/><path d="M3 12h18M12 3c3 3 3 15 0 18M12 3c-3 3-3 15 0 18" fill="none" stroke="#fff" stroke-width="1.6"/></svg></span>
    </div>
    <p class="contact-lines">555 318-0476<br>info@falcridgehires.com<br>www.falcridgehires.com</p>
  </div>

  <ul class="services">
    <li>Weddings</li><li>Concerts</li><li>Events</li><br>
    <li>Charity</li><li>Sporting and Corp</li><br>
    <li>Luxury Restroom Trailers Rental and Sales</li>
  </ul>
</section>

</body>
</html>
```